we can communicate on this, but i want to follow the approach we took on Pellew|Marsh & Quinlan but i feel the card front needs the black background and the platinum and gold logo. The back? I am open. we can use the same info from PM&Q. Velmont Arc is an enhanced equity investment fund - basically a very exclusive boutique hedge fund that uses only stock options. very advanced things. hope you are interested

Contact Information for Business Card

Dr. Lewis T. Brennick, CFA
Scientifique de fusée financière
701.555.0143
LTBquant47@mailvantor.com

4718 Willow Creek Bend W.
West Fargo, ND 58078

No web site

Colors

Designer to choose colors to be used in the design.

Requirements
Nice to have
• I tend to prefer the most visible applications of the logo to include logo and name, the logo version with a black background and the gold and platinum components separated by the black. I see this working well for a single side (logo and name - this is card front to me).
• I am fairly open to other treatments on the reverse side with the data. To me, it makes sense to have a different color rendition of the logo on the reverse and it may be a muted black tone on tone or an oversized portion that would have spot UV. Or, the reverse may play with colors and layout
Should not have
• Other colors = no no
• Decorative font

```html
<!DOCTYPE html>
<html lang="en">
<head>
<meta charset="UTF-8">
<title>Velmont Arc — Business Card</title>
<link rel="stylesheet" href="https://fonts.googleapis.com/css2?family=Montserrat:wght@300;400;600&family=Oswald:wght@500&display=swap">
<style>
  :root {
    --bg: #0e0e0e;
    --card: #1a1a1a;
    --card-edge: #262626;
    --platinum: #dcdcdc;
    --gold: #c9a24d;
    --emboss: #101010;
    --emboss-light: #333333;
    --muted: #4a4a4a;
    --text: #e6e6e6;
    --rule: #4a4a4a;
  }
  * { box-sizing: border-box; margin: 0; padding: 0; }
  html, body {
    width: 1200px;
    height: 900px;
    overflow: hidden;
    background: var(--bg);
  }
  .canvas {
    position: relative;
    width: 1200px;
    height: 900px;
    background: radial-gradient(ellipse at 60% 45%, #1a1a1a 0%, var(--bg) 70%);
  }
  .card {
    position: absolute;
    left: 280px;
    width: 640px;
    height: 366px;
    background: linear-gradient(135deg, var(--card) 0%, #1e1e1e 60%, #272727 100%);
    border: 1px solid var(--card-edge);
    box-shadow: 0 18px 40px rgba(0,0,0,0.6);
  }
  .card--front { top: 64px; }
  .card--back { top: 466px; }

  /* Front */
  .brand {
    position: absolute;
    left: 0; right: 0;
    top: 70px;
    display: flex;
    flex-direction: column;
    align-items: center;
  }
  .brand__mark {
    width: 112px;
    height: 112px;
    border-radius: 50%;
    background: var(--gold);
  }
  .brand__name {
    margin-top: 16px;
    font-family: "Montserrat", sans-serif;
    font-weight: 600;
    font-size: 46px;
    letter-spacing: 2px;
    line-height: 1;
    color: var(--platinum);
    text-transform: uppercase;
  }
  .brand__sub {
    margin-top: 8px;
    font-family: "Montserrat", sans-serif;
    font-weight: 600;
    font-size: 20px;
    letter-spacing: 7px;
    line-height: 1;
    color: var(--platinum);
    text-transform: uppercase;
  }

  /* Back */
  .person {
    position: absolute;
    left: 30px;
    top: 104px;
    width: 282px;
    text-align: right;
  }
  .person__name {
    font-family: "Oswald", sans-serif;
    font-weight: 500;
    font-size: 30px;
    line-height: 1.1;
    color: var(--emboss);
    text-shadow: 1px 1px 0 var(--emboss-light);
    text-transform: uppercase;
  }
  .person__name span { display: block; white-space: nowrap; }
  .person__title {
    margin-top: 4px;
    font-family: "Montserrat", sans-serif;
    font-weight: 400;
    font-size: 14px;
    white-space: nowrap;
    color: var(--muted);
  }
  .divider {
    position: absolute;
    left: 330px;
    top: 104px;
    width: 1px;
    height: 96px;
    background: var(--rule);
  }
  .contact {
    position: absolute;
    left: 350px;
    top: 126px;
    list-style: none;
  }
  .contact__item {
    display: flex;
    align-items: center;
    gap: 10px;
    height: 28px;
    font-family: "Montserrat", sans-serif;
    font-weight: 400;
    font-size: 16px;
    letter-spacing: 0.3px;
    white-space: nowrap;
    color: var(--text);
  }
  .contact__icon {
    width: 14px;
    height: 14px;
    flex: none;
  }
  .address {
    position: absolute;
    left: 58px;
    bottom: 40px;
    font-family: "Montserrat", sans-serif;
    font-weight: 400;
    font-size: 17px;
    letter-spacing: 0.3px;
    white-space: nowrap;
    color: var(--muted);
  }
</style>
</head>
<body>
<main class="canvas">

  <section class="card card--front" aria-label="Card front">
    <div class="brand">
      <div class="brand__mark"></div>
      <div class="brand__name">Velmont</div>
      <div class="brand__sub">Arc</div>
    </div>
  </section>

  <section class="card card--back" aria-label="Card back">
    <div class="person">
      <h1 class="person__name"><span>Dr. Lewis T.</span><span>Brennick, CFA</span></h1>
      <p class="person__title">Scientifique de fusée financière</p>
    </div>

    <div class="divider"></div>

    <ul class="contact">
      <li class="contact__item">
        <svg class="contact__icon" viewBox="0 0 14 14" aria-hidden="true">
          <path d="M3 1 L5 1 L6 4 L4.5 5.2 C5.3 7 6.8 8.6 8.8 9.5 L10 8 L13 9 L13 11 C13 12.2 12 13 11 13 C5.5 12.5 1.5 8.5 1 3 C1 2 1.8 1 3 1 Z" fill="var(--text)"/>
        </svg>
        701.555.0143
      </li>
      <li class="contact__item">
        <svg class="contact__icon" viewBox="0 0 14 14" aria-hidden="true">
          <rect x="1" y="3" width="12" height="8" fill="none" stroke="var(--text)" stroke-width="1.2"/>
          <path d="M1 3 L7 8 L13 3" fill="none" stroke="var(--text)" stroke-width="1.2"/>
        </svg>
        LTBquant47@mailvantor.com
      </li>
    </ul>

    <p class="address">4718 Willow Creek Bend W., West Fargo, ND 58078</p>
  </section>

</main>
</body>
</html>
```